Investment firm needs refreshed corporate powerpoint slides design

We need a new and refreshed powerpoint template for our corporate investment deck. We are a technology private equity group that primarily invests in fast growing software companies and we would like to reflect that in a modern and light blue / transparant / white powerpoint and fonts template. I have also attached our old investor deck as a guideline and also check out our website to get an idea of what we do and what type of companies we invested in. Please note that our website is old and so our presentation should be a refreshed "2017" modern design, not a copy / paste of our website design and graphics.
Updates

Project Deadline Extended Reason: I'm extending the deadline to February 27, but we would ideally receive something by the end of this week.Please submit updates. Thanks Added Tuesday, February 21, 2017

Target Market(s)

Investors such as high net worth individuals, pension funds, banks, financial advisors

Industry/Entity Type

Investment

Colors
33a6d7
85cae6
cfeae6
edf8f6
ffffff
fff3d1
86cfc6

Requirements
Must have
• We let you be creative, we trust you have seen more investment presentations before.
Nice to have
• Pre-built models, flow charts, graphs, charts, etc.
Should not have
• Fancy or edgy images, this has to be a modern, fresh and trustworthy looking powerpoint template. No stock images, if you do use stock images for background purposes please be creative! :-)

```html
<!DOCTYPE html>
<html lang="en">
<head>
<meta charset="utf-8">
<title>Alder — Corporate Deck Slides</title>
<link href="https://fonts.googleapis.com/css2?family=Poppins:wght@400;500;600&display=swap" rel="stylesheet">
<style>
:root{
  --blue:#5b9ec7;
  --sky:#33a6d7;
  --light:#85cae6;
  --mint:#cfeae6;
  --pale:#edf8f6;
  --teal:#86cfc6;
  --navy:#1b4470;
  --ink:#1e6f93;
  --brand:#2a5d75;
  --grey:#a8a8a8;
  --text:#9aa3a8;
  --canvas:#eef1f3;
}
*{margin:0;padding:0;box-sizing:border-box}
html,body{width:1094px;height:1200px;overflow:hidden}
body{background:var(--canvas);font-family:"Poppins",sans-serif;position:relative}
.slide{position:absolute;width:342px;height:193px;background:#fff;overflow:hidden;box-shadow:0 1px 4px rgba(0,0,0,.12)}
.slide::before{content:"";position:absolute;left:0;top:14px;border-left:7px solid #c9cfd3;border-top:7px solid transparent;border-bottom:7px solid transparent}
.c0{left:11px}.c1{left:375px}.c2{left:740px}
.r0{top:6px}.r1{top:204px}.r2{top:403px}.r3{top:601px}.r4{top:799px}.r5{top:997px}
.title{position:absolute;left:15px;top:10px;font-weight:600;font-size:15px;color:var(--ink);white-space:nowrap}
.title::after{content:"";display:block;width:16px;height:2px;background:var(--teal);margin-top:1px}
.brand{position:absolute;right:11px;top:8px;font-weight:400;font-size:16px;color:var(--brand)}
.foot{position:absolute;left:3px;right:14px;bottom:6px;height:9px;background:var(--blue);color:#fff;font-size:3.2px;line-height:9px;padding:0 3px}
.foot .pg{position:absolute;right:4px;top:0}
.tab{position:absolute;right:3px;bottom:6px;width:9px;height:9px;background:var(--teal)}
.lead{position:absolute;font-weight:600;font-size:7.5px;line-height:1.35;color:var(--navy)}
.p{position:absolute;font-size:4px;line-height:1.5;color:var(--text)}
.h{position:absolute;font-weight:500;font-size:6.5px;color:var(--ink)}
.it{position:absolute;font-size:5px;color:var(--ink)}
.it span{display:block;font-size:3.6px;line-height:1.4;color:var(--text)}
.ico{position:absolute;width:11px;height:11px;border-radius:50%;background:var(--blue)}
.ico::after{content:"";position:absolute;left:3px;top:3px;width:5px;height:5px;border-radius:50%;border:1.2px solid #fff;box-sizing:border-box}
.ico.t{background:var(--teal)}.ico.g{background:var(--grey)}
.photo{position:absolute}
.num{position:absolute;left:179px;width:148px;height:26px;color:#fff;font-size:15px;line-height:26px;padding-left:7px}
.num span{position:absolute;left:30px;top:5px;font-size:3.8px;line-height:1.4;width:110px}
.num::after{content:"";position:absolute;left:22px;top:5px;width:1px;height:16px;background:#fff}
</style>
</head>
<body>

<!-- Row 1 -->
<section class="slide c0 r0">
  <h2 class="title">Your Title Goes Here</h2><div class="brand">Alder</div>
  <p class="lead" style="left:27px;top:63px;width:120px">This is place for your header text. Insert your text here, just replace this text with your own text</p>
  <p class="p" style="left:27px;top:108px;width:125px">Lorem ipsum dolor sit amet, consectetur adipiscing elit, sed do eiusmod tempor incididunt ut labore et dolore magna aliqua. Ut enim ad minim veniam, quis nostrud exercitation.</p>
  <p class="p" style="left:27px;top:148px;width:125px">Excepteur sint occaecat cupidatat non proident, sunt in culpa qui officia deserunt mollit anim id est laborum.</p>
  <div class="photo" role="img" aria-label="Office tower and city view in cool blue tones" style="left:171px;top:60px;width:50px;height:110px;background:linear-gradient(160deg,#e9f3f8,#8ab8d4)"></div>
  <div class="photo" role="img" aria-label="Business charts on a desk" style="left:227px;top:60px;width:50px;height:110px;background:linear-gradient(160deg,#f1f6f9,#6aa3c6)"></div>
  <div class="photo" role="img" aria-label="Businessman by a bright window" style="left:283px;top:60px;width:50px;height:110px;background:linear-gradient(160deg,#eef5f8,#4f8fb8)"></div>
  <div class="foot">© 2017 ALDER. All rights reserved<span class="pg">16</span></div><div class="tab"></div>
</section>

<section class="slide c1 r0">
  <h2 class="title">Portfolio Area</h2>
  <div class="h" style="left:18px;top:44px">Heading Goes Here</div>
  <p class="p" style="left:18px;top:52px;width:135px">Lorem ipsum dolor sit amet, consectetur adipiscing elit, sed do eiusmod tempor incididunt ut labore et dolore magna aliqua commodo.</p>
  <div class="ico" style="left:27px;top:78px"></div><div class="it" style="left:48px;top:77px">Your Text Here<span>Lorem ipsum dolor sit amet, adipiscing elit sed do</span></div>
  <div class="ico" style="left:27px;top:102px"></div><div class="it" style="left:48px;top:101px">Your Text Here<span>Lorem ipsum dolor sit amet, adipiscing elit sed do</span></div>
  <div class="ico" style="left:27px;top:126px"></div><div class="it" style="left:48px;top:125px">Your Text Here<span>Lorem ipsum dolor sit amet, adipiscing elit sed do</span></div>
  <div class="ico" style="left:27px;top:151px"></div><div class="it" style="left:48px;top:150px">Your Text Here<span>Lorem ipsum dolor sit amet, adipiscing elit sed do</span></div>
  <div class="photo" role="img" aria-label="Business meeting silhouettes in a glass office" style="left:171px;top:5px;width:84px;height:86px;background:linear-gradient(180deg,#dfe8ee,#7d8a94)"></div>
  <div class="photo" role="img" aria-label="Silhouette by a window" style="left:258px;top:5px;width:83px;height:86px;background:linear-gradient(180deg,#e6edf2,#6c7882)"></div>
  <div class="photo" role="img" aria-label="Financial charts on a table" style="left:171px;top:94px;width:84px;height:84px;background:linear-gradient(180deg,#8a97a0,#2d3439)"></div>
  <div class="photo" role="img" aria-label="Pen over printed charts" style="left:258px;top:94px;width:83px;height:84px;background:linear-gradient(180deg,#98a4ac,#353d42)"></div>
  <div class="foot">© 2017 ALDER. All rights reserved<span class="pg">17</span></div><div class="tab"></div>
</section>

<section class="slide c2 r0">
  <h2 class="title">Our Differences</h2><div class="brand">Alder</div>
  <div style="position:absolute;left:18px;top:58px;width:304px;height:99px;background:var(--blue)">
    <div class="ico" style="left:15px;top:13px;background:#fff;width:10px;height:10px"></div><p class="p" style="left:35px;top:13px;width:130px;color:#fff">Lorem ipsum dolor sit amet, consectetur adipiscing elit, sed do eiusmod tempor ut labore.</p>
    <div class="ico" style="left:15px;top:33px;background:#fff;width:10px;height:10px"></div><p class="p" style="left:35px;top:33px;width:130px;color:#fff">Duis aute irure dolor in reprehenderit in voluptate velit esse cillum dolore.</p>
    <div class="ico" style="left:15px;top:53px;background:#fff;width:10px;height:10px"></div><p class="p" style="left:35px;top:53px;width:130px;color:#fff">Lorem ipsum dolor sit amet, consectetur adipiscing elit, sed do eiusmod tempor labore.</p>
    <div class="ico" style="left:15px;top:73px;background:#fff;width:10px;height:10px"></div><p class="p" style="left:35px;top:73px;width:130px;color:#fff">Duis aute irure dolor in reprehenderit in voluptate velit esse cillum dolore.</p>
    <div class="photo" role="img" aria-label="Businessman standing by a window with charts" style="left:180px;top:13px;width:116px;height:76px;background:linear-gradient(160deg,#f2f7fa,#9cc3da)"></div>
  </div>
  <div class="foot">© 2017 ALDER. All rights reserved<span class="pg">18</span></div><div class="tab"></div>
</section>

<!-- Row 2 -->
<section class="slide c0 r1">
  <h2 class="title">Two Column Description</h2><div class="brand">Alder</div>
  <p class="lead" style="left:18px;top:61px;width:290px">This is place for your header text. Insert your text here, just replace this text with your own text</p>
  <p class="p" style="left:18px;top:92px;width:140px">Lorem ipsum dolor sit amet, consectetur adipiscing elit, sed do eiusmod tempor incididunt ut labore et dolore magna aliqua. Ut enim ad minim veniam, quis nostrud exercitation ullamco laboris nisi ut aliquip ex ea commodo consequat.</p>
  <p class="p" style="left:18px;top:133px;width:140px">Duis aute irure dolor in reprehenderit in voluptate velit esse cillum dolore eu fugiat nulla pariatur. Excepteur sint occaecat cupidatat non proident, sunt in culpa qui officia deserunt mollit anim id est laborum.</p>
  <p class="p" style="left:186px;top:92px;width:140px">Lorem ipsum dolor sit amet, consectetur adipiscing elit, sed do eiusmod tempor incididunt ut labore et dolore magna aliqua. Ut enim ad minim veniam, quis nostrud exercitation ullamco laboris nisi ut aliquip ex ea commodo consequat.</p>
  <p class="p" style="left:186px;top:133px;width:140px">Duis aute irure dolor in reprehenderit in voluptate velit esse cillum dolore eu fugiat nulla pariatur. Excepteur sint occaecat cupidatat non proident, sunt in culpa qui officia deserunt mollit anim id est laborum.</p>
  <div class="foot">© 2017 ALDER. All rights reserved<span class="pg">19</span></div><div class="tab"></div>
</section>

<section class="slide c1 r1" role="img" aria-label="Calm sea horizon in soft teal blue" style="background:linear-gradient(180deg,#5f9fc0 0%,#6cb0c0 55%,#7fc6c0 100%)">
  <div class="brand" style="color:#fff;top:14px">Alder</div>
  <svg style="position:absolute;left:81px;top:65px" width="18" height="18" viewBox="0 0 18 18" fill="none" stroke="#fff" stroke-width="1.4"><path d="M3 8h10v3a4 4 0 0 1-4 4h-2a4 4 0 0 1-4-4z"/><path d="M13 9h2a2 2 0 0 1 0 4h-2"/><path d="M2 16.5h13"/><path d="M7 2c-1 1.5 1 2.5 0 4M10 2c-1 1.5 1 2.5 0 4"/></svg>
  <div style="position:absolute;left:0;width:200px;top:87px;text-align:center;color:#fff;font-weight:500;font-size:11px">COFFEE BREAK</div>
  <div style="position:absolute;left:0;width:200px;top:101px;text-align:center;color:#eaf6f7;font-size:5px">Back in 15 minutes</div>
</section>

<section class="slide c2 r1">
  <h2 class="title">Three Column Description</h2><div class="brand">Alder</div>
  <p class="lead" style="left:18px;top:48px;width:290px">This is place for your header text. Insert your text here, just replace this text with your own text</p>
  <p class="p" style="left:18px;top:77px;width:92px">Lorem ipsum dolor sit amet, consectetur adipiscing elit, sed do eiusmod tempor incididunt ut labore et dolore magna aliqua. Ut enim ad minim veniam, quis nostrud exercitation laboris nisi ut aliquip ex ea commodo consequat.</p>
  <p class="p" style="left:18px;top:140px;width:92px">Duis aute irure dolor in reprehenderit in voluptate velit esse cillum dolore eu fugiat nulla pariatur excepteur occaecat.</p>
  <p class="p" style="left:127px;top:77px;width:92px">Lorem ipsum dolor sit amet, consectetur adipiscing elit, sed do eiusmod tempor incididunt ut labore et dolore magna aliqua. Ut enim ad minim veniam, quis nostrud exercitation laboris nisi ut aliquip ex ea commodo consequat.</p>
  <p class="p" style="left:127px;top:140px;width:92px">Duis aute irure dolor in reprehenderit in voluptate velit esse cillum dolore eu fugiat nulla pariatur excepteur occaecat.</p>
  <p class="p" style="left:236px;top:77px;width:92px">Lorem ipsum dolor sit amet, consectetur adipiscing elit, sed do eiusmod tempor incididunt ut labore et dolore magna aliqua. Ut enim ad minim veniam, quis nostrud exercitation laboris nisi ut aliquip ex ea commodo consequat.</p>
  <p class="p" style="left:236px;top:140px;width:92px">Duis aute irure dolor in reprehenderit in voluptate velit esse cillum dolore eu fugiat nulla pariatur excepteur occaecat.</p>
  <div class="foot">© 2017 ALDER. All rights reserved<span class="pg">21</span></div><div class="tab"></div>
</section>

<!-- Row 3 -->
<section class="slide c0 r2">
  <div class="photo" role="img" aria-label="Modern glass and steel atrium in grey tones" style="left:0;top:0;width:342px;height:193px;background:linear-gradient(135deg,#d9dcde 0%,#8d9296 45%,#5c6165 100%)"></div>
  <div style="position:absolute;left:203px;top:0;width:122px;height:193px;background:rgba(91,158,199,.85)"></div>
  <div style="position:absolute;left:203px;top:176px;width:122px;height:17px;background:var(--navy);color:#fff;font-size:4.5px;line-height:17px;text-align:center">www.yourwebsite.com</div>
  <div class="brand" style="right:31px;top:16px;font-size:22px;color:#fff">Alder</div>
  <div class="ico" style="left:216px;top:64px;background:none;border:1px solid #fff;width:16px;height:16px"></div>
  <div class="ico" style="left:248px;top:64px;background:none;border:1px solid #fff;width:16px;height:16px"></div>
  <div class="ico" style="left:280px;top:64px;background:none;border:1px solid #fff;width:16px;height:16px"></div>
  <div style="position:absolute;left:217px;top:105px;color:#fff;font-weight:500;font-size:13px;line-height:1.1">Your Title<br>Goes Here</div>
  <p class="p" style="left:217px;top:136px;width:100px;color:#fff">Lorem ipsum dolor sit amet, consectetur adipiscing elit, sed do eiusmod tempor incididunt ut labore et dolore commodo consequat magna aliqua.</p>
</section>

<section class="slide c1 r2">
  <h2 class="title">Your Title Goes Here</h2><div class="brand">Alder</div>
  <div class="h" style="left:15px;top:44px">Heading Goes Here</div>
  <p class="p" style="left:15px;top:52px;width:315px">Lorem ipsum dolor sit amet, consectetur adipiscing elit, sed do eiusmod tempor incididunt ut labore et dolore magna aliqua. Ut enim ad minim veniam, quis nostrud exercitation ullamco laboris nisi ut aliquip ex ea commodo consequat.</p>
  <div class="ico" style="left:16px;top:72px"></div><div class="it" style="left:39px;top:71px;color:var(--sky)">Service Number One<span style="width:110px">Lorem ipsum dolor sit amet, consectetur adipiscing elit, sed do eiusmod tempor incididunt ut labore dolore.</span></div>
  <div class="ico t" style="left:16px;top:104px"></div><div class="it" style="left:39px;top:103px;color:var(--teal)">Service Number Two<span style="width:110px">Lorem ipsum dolor sit amet, consectetur adipiscing elit, sed do eiusmod tempor incididunt ut labore dolore.</span></div>
  <div class="ico g" style="left:16px;top:137px"></div><div class="it" style="left:39px;top:136px;color:var(--grey)">Service Number Three<span style="width:110px">Lorem ipsum dolor sit amet, consectetur adipiscing elit, sed do eiusmod tempor incididunt ut labore dolore.</span></div>
  <div class="num" style="top:69px;background:var(--blue)">1<span>Lorem ipsum dolor sit amet, consectetur adipiscing elit, sed do eiusmod tempor incididunt ut labore et dolore magna.</span></div>
  <div class="num" style="top:101px;background:#6cc4b6">2<span>Lorem ipsum dolor sit amet, consectetur adipiscing elit, sed do eiusmod tempor incididunt ut labore et dolore magna.</span></div>
  <div class="num" style="top:134px;background:var(--grey)">3<span>Lorem ipsum dolor sit amet, consectetur adipiscing elit, sed do eiusmod tempor incididunt ut labore et dolore magna.</span></div>
  <div class="foot">© 2017 ALDER. All rights reserved<span class="pg">23</span></div><div class="tab"></div>
</section>

<section class="slide c2 r2">
  <h2 class="title">Four Bullets with Paragraph</h2><div class="brand">Alder</div>
  <div class="ico" style="left:21px;top:64px"></div><div class="it" style="left:39px;top:62px">Your Text Here<span style="width:45px">Lorem ipsum dolor sit amet, consectetur adipiscing elit, sed do eiusmod</span></div>
  <div class="ico" style="left:97px;top:64px"></div><div class="it" style="left:115px;top:62px">Your Text Here<span style="width:45px">Lorem ipsum dolor sit amet, consectetur adipiscing elit, sed do eiusmod</span></div>
  <div class="ico" style="left:21px;top:120px"></div><div class="it" style="left:39px;top:118px">Your Text Here<span style="width:45px">Lorem ipsum dolor sit amet, consectetur adipiscing elit, sed do eiusmod</span></div>
  <div class="ico" style="left:97px;top:120px"></div><div class="it" style="left:115px;top:118px">Your Text Here<span style="width:45px">Lorem ipsum dolor sit amet, consectetur adipiscing elit, sed do eiusmod</span></div>
  <div class="h" style="left:187px;top:62px">Heading Goes Here</div>
  <p class="p" style="left:187px;top:72px;width:140px">Lorem ipsum dolor sit amet, consectetur adipiscing elit, sed do eiusmod tempor incididunt ut labore et dolore magna aliqua.</p>
  <p class="p" style="left:187px;top:100px;width:140px">Duis aute irure dolor in reprehenderit in voluptate velit esse cillum dolore eu fugiat nulla pariatur.</p>
  <p class="p" style="left:187px;top:120px;width:140px">Ut enim ad minim veniam, quis nostrud exercitation ullamco laboris nisi ut aliquip ex ea commodo consequat.</p>
  <div class="foot">© 2017 ALDER. All rights reserved<span class="pg">24</span></div><div class="tab"></div>
</section>

<!-- Row 4 -->
<section class="slide c0 r3">
  <h2 class="title">Your Title</h2><div class="brand">Alder</div>
  <div class="photo" role="img" aria-label="Two business people talking in a bright office" style="left:110px;top:0;width:120px;height:179px;background:linear-gradient(180deg,#f4f7f9,#c9d6df 60%,#9fb8c9)"></div>
  <div class="h" style="left:14px;top:60px">Heading Goes Here</div>
  <p class="p" style="left:14px;top:70px;width:90px">Lorem ipsum dolor sit amet, consectetur adipiscing elit, sed do eiusmod tempor incididunt ut labore et commodo consequat dolore magna aliqua.</p>
  <p class="p" style="left:14px;top:106px;width:90px">Duis aute irure dolor in reprehenderit in voluptate velit esse cillum dolore eu fugiat nulla pariatur.</p>
  <p class="p" style="left:14px;top:132px;width:90px">Ut enim ad minim veniam, quis nostrud exercitation ullamco laboris nisi ut aliquip ex ea commodo consequat.</p>
  <div class="ico" style="left:243px;top:59px"></div><div class="it" style="left:263px;top:58px">Your Text Here<span style="width:60px">Lorem ipsum dolor sit amet, adipiscing elit sed do</span></div>
  <div class="ico" style="left:243px;top:87px"></div><div class="it" style="left:263px;top:86px">Your Text Here<span style="width:60px">Lorem ipsum dolor sit amet, adipiscing elit sed do</span></div>
  <div class="ico" style="left:243px;top:115px"></div><div class="it" style="left:263px;top:114px">Your Text Here<span style="width:60px">Lorem ipsum dolor sit amet, adipiscing elit sed do</span></div>
  <div class="ico" style="left:243px;top:143px"></div><div class="it" style="left:263px;top:142px">Your Text Here<span style="width:60px">Lorem ipsum dolor sit amet, adipiscing elit sed do</span></div>
  <div class="foot">© 2017 ALDER. All rights reserved<span class="pg">25</span></div><div class="tab"></div>
</section>

<section class="slide c1 r3">
  <h2 class="title">Text &amp; Bullet Area</h2><div class="brand">Alder</div>
  <div class="h" style="left:17px;top:58px">Heading Goes Here</div>
  <p class="p" style="left:17px;top:68px;width:90px">Lorem ipsum dolor sit amet, consectetur adipiscing elit, sed do eiusmod tempor incididunt ut labore et commodo consequat dolore magna aliqua.</p>
  <p class="p" style="left:17px;top:103px;width:90px">Duis aute irure dolor in reprehenderit in voluptate velit esse cillum dolore eu fugiat nulla pariatur.</p>
  <p class="p" style="left:17px;top:128px;width:90px">Ut enim ad minim veniam, quis nostrud exercitation ullamco laboris nisi ut aliquip ex ea commodo consequat.</p>
  <div class="ico" style="left:128px;top:58px"></div><div class="it" style="left:148px;top:57px">Your Text Here<span style="width:70px">Lorem ipsum dolor sit amet, consectetur adipiscing elit, sed do eiusmod</span></div>
  <div class="ico" style="left:128px;top:86px"></div><div class="it" style="left:148px;top:85px">Your Text Here<span style="width:70px">Lorem ipsum dolor sit amet, consectetur adipiscing elit, sed do eiusmod</span></div>
  <div class="ico" style="left:128px;top:114px"></div><div class="it" style="left:148px;top:113px">Your Text Here<span style="width:70px">Lorem ipsum dolor sit amet, consectetur adipiscing elit, sed do eiusmod</span></div>
  <div class="ico" style="left:128px;top:142px"></div><div class="it" style="left:148px;top:141px">Your Text Here<span style="width:70px">Lorem ipsum dolor sit amet, consectetur adipiscing elit, sed do eiusmod</span></div>
  <div class="ico" style="left:236px;top:58px"></div><div class="it" style="left:256px;top:57px">Your Text Here<span style="width:70px">Lorem ipsum dolor sit amet, consectetur adipiscing elit, sed do eiusmod</span></div>
  <div class="ico" style="left:236px;top:86px"></div><div class="it" style="left:256px;top:85px">Your Text Here<span style="width:70px">Lorem ipsum dolor sit amet, consectetur adipiscing elit, sed do eiusmod</span></div>
  <div class="ico" style="left:236px;top:114px"></div><div class="it" style="left:256px;top:113px">Your Text Here<span style="width:70px">Lorem ipsum dolor sit amet, consectetur adipiscing elit, sed do eiusmod</span></div>
  <div class="ico" style="left:236px;top:142px"></div><div class="it" style="left:256px;top:141px">Your Text Here<span style="width:70px">Lorem ipsum dolor sit amet, consectetur adipiscing elit, sed do eiusmod</span></div>
  <div class="foot">© 2017 ALDER. All rights reserved<span class="pg">26</span></div><div class="tab"></div>
</section>

<section class="slide c2 r3">
  <div class="photo" role="img" aria-label="Steel footbridge perspective washed in blue and teal" style="left:0;top:0;width:342px;height:193px;background:linear-gradient(180deg,#5f9fc3 0%,#6fb0c4 55%,#86cfc6 100%)"></div>
  <div class="brand" style="color:#fff;font-size:22px;top:18px">Alder</div>
  <div style="position:absolute;left:8px;top:99px;color:#e4f2f5;font-size:4.5px">Divider Page</div>
  <div style="position:absolute;left:8px;top:105px;color:#fff;font-weight:500;font-size:15px">Your Title Goes Here</div>
  <div style="position:absolute;left:49px;top:124px;color:#e4f2f5;font-size:6.5px">Your Subtitle Here</div>
</section>

<!-- Row 5 -->
<section class="slide c0 r4">
  <h2 class="title">Paragraph with Three Bullet</h2><div class="brand">Alder</div>
  <p class="lead" style="left:18px;top:49px;width:290px">This is place for your header text. Insert your text here, just replace this text with your own text</p>
  <p class="p" style="left:18px;top:85px;width:95px">Lorem ipsum dolor sit amet, consectetur adipiscing elit, sed do eiusmod tempor incididunt ut labore et dolore magna aliqua. Ut enim minim veniam quis nostrud exercitation ullamco laboris nisi aliquip commodo consequat.</p>
  <p class="p" style="left:18px;top:137px;width:95px">Duis aute irure dolor in reprehenderit in voluptate velit esse cillum dolore eu fugiat nulla pariatur excepteur occaecat.</p>
  <div style="position:absolute;left:121px;top:85px;width:1px;height:80px;background:#e3e8eb"></div>
  <div class="ico" style="left:157px;top:84px;background:none;border:1px solid var(--blue);width:14px;height:14px"></div>
  <div class="ico" style="left:225px;top:84px;background:none;border:1px solid var(--blue);width:14px;height:14px"></div>
  <div class="ico" style="left:293px;top:84px;background:none;border:1px solid var(--blue);width:14px;height:14px"></div>
  <div class="it" style="left:138px;top:103px;width:55px;text-align:center;font-size:4px">Your Text Here<span>Lorem ipsum dolor sit amet, consectetur adipiscing elit, sed do eiusmod tempor labore aliqua.</span><span style="margin-top:3px">Ut enim minim veniam, quis nostrud exercitation ullamco commodo consequat.</span></div>
  <div class="it" style="left:206px;top:103px;width:55px;text-align:center;font-size:4px">Your Text Here<span>Lorem ipsum dolor sit amet, consectetur adipiscing elit, sed do eiusmod tempor labore aliqua.</span><span style="margin-top:3px">Ut enim minim veniam, quis nostrud exercitation ullamco commodo consequat.</span></div>
  <div class="it" style="left:274px;top:103px;width:55px;text-align:center;font-size:4px">Your Text Here<span>Lorem ipsum dolor sit amet, consectetur adipiscing elit, sed do eiusmod tempor labore aliqua.</span><span style="margin-top:3px">Ut enim minim veniam, quis nostrud exercitation ullamco commodo consequat.</span></div>
  <div class="foot">© 2017 ALDER. All rights reserved<span class="pg">28</span></div><div class="tab"></div>
</section>

<section class="slide c1 r4">
  <h2 class="title">Global Experience</h2><div class="brand">Alder</div>
  <div class="photo" role="img" aria-label="World map in light grey with office locations marked" style="left:85px;top:33px;width:235px;height:120px;border-radius:40px;background:radial-gradient(ellipse at center,#c6cbce 0%,#dfe2e4 60%,#fff 75%)"></div>
  <div class="ico" style="left:15px;top:147px;width:12px;height:12px"></div>
  <div class="h" style="left:32px;top:148px;font-size:5.5px">Heading Goes Here</div>
  <p class="p" style="left:15px;top:160px;width:190px">Lorem ipsum dolor sit amet, consectetur adipiscing elit, sed do eiusmod tempor incididunt ut labore et dolore magna aliqua.</p>
  <div class="foot">© 2017 ALDER. All rights reserved<span class="pg">29</span></div><div class="tab"></div>
</section>

<section class="slide c2 r4">
  <h2 class="title">Multiple Column Area</h2><div class="brand">Alder</div>
  <div class="ico" style="left:38px;top:52px;width:13px;height:13px"></div>
  <div class="ico t" style="left:101px;top:52px;width:13px;height:13px"></div>
  <div class="ico" style="left:164px;top:52px;width:13px;height:13px"></div>
  <div class="ico t" style="left:227px;top:52px;width:13px;height:13px"></div>
  <div class="ico" style="left:290px;top:52px;width:13px;height:13px"></div>
  <div class="it" style="left:20px;top:69px;width:50px;text-align:center;font-size:4.5px">Your Text Here<span>Lorem ipsum consectetur adipiscing elit</span></div>
  <div class="it" style="left:83px;top:69px;width:50px;text-align:center;font-size:4.5px">Your Text Here<span>Lorem ipsum consectetur adipiscing elit</span></div>
  <div class="it" style="left:146px;top:69px;width:50px;text-align:center;font-size:4.5px">Your Text Here<span>Lorem ipsum consectetur adipiscing elit</span></div>
  <div class="it" style="left:209px;top:69px;width:50px;text-align:center;font-size:4.5px">Your Text Here<span>Lorem ipsum consectetur adipiscing elit</span></div>
  <div class="it" style="left:272px;top:69px;width:50px;text-align:center;font-size:4.5px">Your Text Here<span>Lorem ipsum consectetur adipiscing elit</span></div>
  <div style="position:absolute;left:24px;top:97px;width:296px;height:1px;background:#e3e8eb"></div>
  <div class="h" style="left:24px;top:114px">Heading Goes Here</div>
  <p class="p" style="left:24px;top:123px;width:135px">Lorem ipsum dolor sit amet, consectetur adipiscing elit, sed do eiusmod tempor incididunt ut labore et commodo consequat dolore magna aliqua.</p>
  <p class="p" style="left:24px;top:146px;width:135px">Duis aute irure dolor in reprehenderit in voluptate velit esse cillum dolore eu fugiat nulla pariatur.</p>
  <div class="h" style="left:184px;top:114px">Heading Goes Here</div>
  <p class="p" style="left:184px;top:123px;width:135px">Lorem ipsum dolor sit amet, consectetur adipiscing elit, sed do eiusmod tempor incididunt ut labore et commodo consequat dolore magna aliqua.</p>
  <p class="p" style="left:184px;top:146px;width:135px">Duis aute irure dolor in reprehenderit in voluptate velit esse cillum dolore eu fugiat nulla pariatur.</p>
  <div class="foot">© 2017 ALDER. All rights reserved<span class="pg">30</span></div><div class="tab"></div>
</section>

<!-- Row 6 -->
<section class="slide c0 r5">
  <h2 class="title">Your Pie Chart Area</h2><div class="brand">Alder</div>
  <svg style="position:absolute;left:0;top:60px" width="342" height="50" viewBox="0 0 342 50" fill="none">
    <g stroke-width="5" font-family="Poppins, sans-serif" font-size="9" text-anchor="middle">
      <circle cx="53" cy="25" r="17" stroke="#e6eaec"/><circle cx="53" cy="25" r="17" stroke="#7aa6c0" stroke-dasharray="21.4 85.4" transform="rotate(-90 53 25)"/><text x="53" y="28" fill="#7aa6c0" stroke="none">20%</text>
      <circle cx="131" cy="25" r="17" stroke="#e6eaec"/><circle cx="131" cy="25" r="17" stroke="#7fd0c4" stroke-dasharray="53.4 106.8" transform="rotate(-90 131 25)"/><text x="131" y="28" fill="#7fd0c4" stroke="none">50%</text>
      <circle cx="209" cy="25" r="17" stroke="#e6eaec"/><circle cx="209" cy="25" r="17" stroke="#85cae6" stroke-dasharray="74.8 106.8" transform="rotate(-90 209 25)"/><text x="209" y="28" fill="#85cae6" stroke="none">70%</text>
      <circle cx="289" cy="25" r="17" stroke="#e6eaec"/><circle cx="289" cy="25" r="17" stroke="#1b4470" stroke-dasharray="32 106.8" transform="rotate(-90 289 25)"/><text x="289" y="28" fill="#1b4470" stroke="none">30%</text>
    </g>
  </svg>
  <div class="it" style="left:28px;top:114px;width:50px;text-align:center;font-size:3.8px;color:var(--navy)">Subtitle in this area<span>Lorem ipsum dolor sit amet, consectetur adipiscing elit integer mollis vehicula ligula.</span></div>
  <div class="it" style="left:106px;top:114px;width:50px;text-align:center;font-size:3.8px;color:var(--navy)">Subtitle in this area<span>Lorem ipsum dolor sit amet, consectetur adipiscing elit integer mollis vehicula ligula.</span></div>
  <div class="it" style="left:184px;top:114px;width:50px;text-align:center;font-size:3.8px;color:var(--navy)">Subtitle in this area<span>Lorem ipsum dolor sit amet, consectetur adipiscing elit integer mollis vehicula ligula.</span></div>
  <div class="it" style="left:264px;top:114px;width:50px;text-align:center;font-size:3.8px;color:var(--navy)">Subtitle in this area<span>Lorem ipsum dolor sit amet, consectetur adipiscing elit integer mollis vehicula ligula.</span></div>
  <div class="foot">© 2017 ALDER. All rights reserved<span class="pg">31</span></div><div class="tab"></div>
</section>

<section class="slide c1 r5">
  <h2 class="title">Your Pie Chart Area</h2><div class="brand">Alder</div>
  <svg style="position:absolute;left:131px;top:58px" width="80" height="80" viewBox="0 0 80 80" fill="none">
    <g transform="rotate(-90 40 40)" stroke-width="17">
      <circle cx="40" cy="40" r="27" stroke="#1b4470" stroke-dasharray="59.4 110.2"/>
      <circle cx="40" cy="40" r="27" stroke="#a8a8a8" stroke-dasharray="25.4 144.2" stroke-dashoffset="-59.4"/>
      <circle cx="40" cy="40" r="27" stroke="#86cfc6" stroke-dasharray="50.9 118.7" stroke-dashoffset="-84.8"/>
      <circle cx="40" cy="40" r="27" stroke="#5b9ec7" stroke-dasharray="33.9 135.7" stroke-dashoffset="-135.7"/>
    </g>
    <g fill="#fff" font-family="Poppins, sans-serif" font-size="6.5" font-weight="600">
      <text x="14" y="22">20%</text><text x="56" y="33">35%</text><text x="46" y="66">40%</text><text x="8" y="53">30%</text>
    </g>
  </svg>
  <div class="ico" style="left:106px;top:56px;width:22px;height:22px;background:var(--blue)"></div>
  <div class="ico" style="left:106px;top:118px;width:22px;height:22px;background:var(--teal)"></div>
  <div class="ico" style="left:217px;top:56px;width:22px;height:22px;background:var(--navy)"></div>
  <div class="ico" style="left:217px;top:118px;width:22px;height:22px;background:var(--grey)"></div>
  <div class="it" style="left:48px;top:57px;width:53px;text-align:right;font-size:3.8px">Secure<span>Nullam eu tempor purus nunc a ex magna sit amet consequat</span></div>
  <div class="it" style="left:48px;top:119px;width:53px;text-align:right;font-size:3.8px">Good Package<span>Nullam eu tempor purus nunc a ex magna sit amet consequat</span></div>
  <div class="it" style="left:245px;top:57px;width:55px;font-size:3.8px;color:var(--navy)">Well Organized<span>Nullam eu tempor purus nunc a ex magna sit amet consequat</span></div>
  <div class="it" style="left:245px;top:119px;width:55px;font-size:3.8px;color:var(--grey)">Publication<span>Nullam eu tempor purus nunc a ex magna sit amet consequat</span></div>
  <p class="p" style="left:55px;top:157px;width:232px;text-align:center;font-size:3.6px">Lorem ipsum dolor sit amet, consectetur adipiscing elit. Sed et consectetur lacus, sed sit amet nulla vel dolor gravida. Nunc odio massa, sodales et consectetur a, iaculis eget purus. Mauris gravida ac faucibus laoreet.</p>
  <div class="foot">© 2017 ALDER. All rights reserved<span class="pg">32</span></div><div class="tab"></div>
</section>

<section class="slide c2 r5">
  <h2 class="title">Your Pie Chart Area</h2><div class="brand">Alder</div>
  <svg style="position:absolute;left:46px;top:38px" width="120" height="80" viewBox="0 0 120 80" fill="none">
    <g transform="translate(60 36) scale(1 .55) rotate(-90)">
      <circle r="25" stroke="#5b9ec7" stroke-width="50" stroke-dasharray="102 157.1"/>
      <circle r="25" stroke="#a8a8a8" stroke-width="50" stroke-dasharray="24 157.1" stroke-dashoffset="-102"/>
      <circle r="25" stroke="#86cfc6" stroke-width="50" stroke-dasharray="31.1 157.1" stroke-dashoffset="-126"/>
    </g>
    <g font-family="Poppins, sans-serif" font-size="3" fill="#5b9ec7"><text x="42" y="76">■ Sales A  ■ Sales B  ■ Sales C</text></g>
  </svg>
  <div class="ico g" style="left:212px;top:45px;width:10px;height:10px"></div><div class="it" style="left:228px;top:44px;color:var(--grey);font-size:4.5px">Your Text Here<span>Lorem ipsum dolor sit amet.</span></div>
  <div class="ico t" style="left:212px;top:69px;width:10px;height:10px"></div><div class="it" style="left:228px;top:68px;color:var(--teal);font-size:4.5px">Your Text Here<span>Lorem ipsum dolor sit amet.</span></div>
  <div class="ico" style="left:212px;top:93px;width:10px;height:10px"></div><div class="it" style="left:228px;top:92px;color:var(--blue);font-size:4.5px">Your Text Here<span>Lorem ipsum dolor sit amet.</span></div>
  <svg style="position:absolute;left:23px;top:140px" width="12" height="10" viewBox="0 0 12 10"><path d="M6 0L12 10H0z" fill="#5b9ec7"/></svg>
  <div style="position:absolute;left:37px;top:136px;color:var(--blue);font-size:14px">54%</div>
  <div class="h" style="left:70px;top:133px;font-size:5.5px;color:var(--navy)">Heading Goes Here</div>
  <p class="p" style="left:70px;top:141px;width:215px">Lorem ipsum adipiscing elit, sed do eiusmod tempor incididunt ut labore et dolore magna aliqua. Ut enim ad minim veniam, quis nostrud exercitation laboris nisi ut aliquip ex ea commodo consequat.</p>
  <div class="foot">© 2017 ALDER. All rights reserved<span class="pg">33</span></div><div class="tab"></div>
</section>

</body>
</html>
```